Business card design for Virtual Assistance company

I need a business card designed for my virtual assistance company. We are a small company who services primarily C-level executive clients. The card needs to be double sided with the following contact information on the back:
Melissa Thornbury
Owner/CEO
info@rkpadvisory.net
www.rkpadvisory.net
555.302.9817

The front side should just have the company name incorporated: "RKP Advisory" and "virtual assistance"

The card should be simplistic, but eye catching and should speak to high level executives. Our primary focus areas consist of executive assistance and government contracting.

Target Market(s)

CEOs and executives

Contact Information for Business Card

see project description. phone, email, website.

Colors

Designer to choose only greyscale colors for use in the design.

```html
<!DOCTYPE html>
<html lang="en">
<head>
<meta charset="utf-8">
<title>RKP Advisory – Business Card</title>
<link rel="stylesheet" href="https://fonts.googleapis.com/css2?family=Crimson+Text:wght@400;600;700&family=Montserrat:wght@400;500&display=swap">
<style>
  :root {
    --stage: #d9d6d1;
    --card: #1b1b1b;
    --card-edge: #111111;
    --ink: #ffffff;
    --ink-soft: #e6e6e6;
    --pattern-light: #3a3a3a;
    --pattern-dark: #121212;
  }
  * { box-sizing: border-box; margin: 0; padding: 0; }
  html, body {
    width: 900px; height: 1200px; overflow: hidden;
    background: var(--stage);
  }
  .canvas { position: relative; width: 900px; height: 1200px; }

  .card {
    position: absolute;
    width: 742px; height: 442px;
    border-radius: 22px;
    background: var(--card);
    overflow: hidden;
    color: var(--ink);
  }
  .card--front { left: 80px; top: 130px; }
  .card--back  { left: 80px; top: 637px; background: var(--card-edge); }

  .company-name {
    position: absolute; left: 34px; top: 36px;
    font-family: "Crimson Text", Georgia, serif;
    font-size: 50px; font-weight: 400; line-height: 1;
  }
  .owner {
    position: absolute; right: 52px; top: 48px; text-align: right;
  }
  .owner__name {
    font-family: "Crimson Text", Georgia, serif;
    font-weight: 700; font-size: 27px; line-height: 1;
  }
  .owner__title {
    font-family: "Montserrat", Arial, sans-serif;
    font-size: 15px; color: var(--ink-soft); margin-top: 6px;
  }

  .contact-list {
    position: absolute; left: 44px; top: 291px; list-style: none;
    font-family: "Montserrat", Arial, sans-serif;
    font-size: 16px; color: var(--ink-soft);
  }
  .contact-list li {
    display: flex; align-items: center; gap: 9px; height: 28px;
  }
  .contact-list svg { width: 16px; height: 16px; fill: var(--ink); flex: none; }

  .tagline {
    position: absolute; left: 45px; top: 391px;
    font-family: "Crimson Text", Georgia, serif;
    font-size: 16px; letter-spacing: 0.3px; text-transform: uppercase;
  }

  .front-mark {
    position: absolute; right: 38px; bottom: 40px;
    font-family: "Crimson Text", Georgia, serif;
    font-size: 46px; font-weight: 400; line-height: 1;
  }

  .back-pattern {
    position: absolute; inset: 0;
    background: linear-gradient(100deg, var(--pattern-light) 0%, #262626 35%, var(--pattern-dark) 65%, var(--pattern-dark) 100%);
  }
  .back-mark {
    position: absolute; right: 84px; top: 270px;
    font-family: "Crimson Text", Georgia, serif;
    font-size: 30px; font-weight: 400; line-height: 1;
  }
</style>
</head>
<body>
<main class="canvas">

  <section class="card card--front" aria-label="Card front">
    <h1 class="company-name">RKP Advisory</h1>
    <div class="owner">
      <p class="owner__name">Melissa Thornbury</p>
      <p class="owner__title">Owner/CEO</p>
    </div>

    <ul class="contact-list">
      <li>
        <svg viewBox="0 0 24 24" aria-hidden="true"><path d="M6.6 10.8a15.1 15.1 0 0 0 6.6 6.6l2.2-2.2a1 1 0 0 1 1-.25 11.4 11.4 0 0 0 3.6.57 1 1 0 0 1 1 1V20a1 1 0 0 1-1 1A17 17 0 0 1 3 4a1 1 0 0 1 1-1h3.5a1 1 0 0 1 1 1c0 1.25.2 2.46.57 3.6a1 1 0 0 1-.25 1z"/></svg>
        <span>555.302.9817</span>
      </li>
      <li>
        <svg viewBox="0 0 24 24" aria-hidden="true"><path d="M2 6.5A1.5 1.5 0 0 1 3.5 5h17A1.5 1.5 0 0 1 22 6.5v.3l-10 6.2L2 6.8zM2 9.1l10 6.2 10-6.2v8.4a1.5 1.5 0 0 1-1.5 1.5h-17A1.5 1.5 0 0 1 2 17.5z"/></svg>
        <span>info@rkpadvisory.net</span>
      </li>
      <li>
        <svg viewBox="0 0 24 24" aria-hidden="true"><path d="M12 2a10 10 0 1 0 0 20 10 10 0 0 0 0-20zm-1 17.9A8 8 0 0 1 4.1 10.9L9 15.8v1a2 2 0 0 0 2 2zm6.9-2.5a2 2 0 0 0-1.9-1.4h-1v-3a1 1 0 0 0-1-1H8v-2h2a1 1 0 0 0 1-1V7h2a2 2 0 0 0 2-2v-.4a8 8 0 0 1 2.9 12.8z"/></svg>
        <span>www.rkpadvisory.net</span>
      </li>
    </ul>

    <p class="tagline">Virtual Assistance</p>
    <p class="front-mark">RKP Advisory</p>
  </section>

  <section class="card card--back" aria-label="Card back">
    <div class="back-pattern" role="img" aria-label="Repeating tone-on-tone company monogram pattern"></div>
    <p class="back-mark">RKP Advisory</p>
  </section>

</main>
</body>
</html>
```